Business Card Design for Occupational Medicine Start Up Company

We need to design a professional business card. We are a healthcare company providing occupational medicine services to blue collar industries. We are professional, efficient and high quality service providers.

Target Market(s)

Blue Collar Industry: Shipbuilding, Ports, Trucking Companies; The Executives and Safety Officers for these companies

Industry/Entity Type

Healthcare

Contact Information for Business Card

Logo, Name, Title, Email, Phone

Other font styles liked:
• Please match our Brand Guide

Requirements
Must have
• Our Company Colors and Logo

```html
<!DOCTYPE html>
<html lang="en">
<head>
<meta charset="utf-8">
<title>Shiftwell Clinics – Business Card</title>
<link href="https://fonts.googleapis.com/css2?family=Montserrat:wght@400;500;700&display=swap" rel="stylesheet">
<style>
  :root {
    --stage: #2a2a2c;
    --navy: #2c3384;
    --navy-deep: #232a70;
    --navy-soft: #4a5bb0;
    --sky: #29a8e0;
    --amber: #f5a83a;
    --white: #ffffff;
  }
  * { box-sizing: border-box; margin: 0; padding: 0; }
  html, body { width: 1200px; height: 874px; overflow: hidden; }
  body {
    background: var(--stage);
    font-family: "Montserrat", sans-serif;
    position: relative;
  }
  .card {
    position: absolute;
    left: 290px;
    width: 620px;
    height: 354px;
    border-radius: 18px;
    overflow: hidden;
  }
  .card--back { top: 43px; background: var(--navy); }
  .card--front { top: 477px; background: var(--white); }

  .back-texture {
    position: absolute; inset: 0;
    background: linear-gradient(115deg, var(--navy-deep) 0%, var(--navy) 50%, var(--navy-soft) 100%);
  }
  .brand {
    position: absolute;
    display: flex;
    align-items: center;
    gap: 14px;
    font-weight: 700;
    letter-spacing: 0.5px;
    line-height: 1.05;
  }
  .brand__dot { border-radius: 50%; flex: none; }
  .card--back .brand { left: 320px; top: 150px; color: var(--white); font-size: 24px; }
  .card--back .brand__dot { width: 46px; height: 46px; background: var(--white); }
  .card--front .brand { left: 40px; top: 58px; color: var(--navy); font-size: 28px; }
  .card--front .brand__dot { width: 52px; height: 52px; background: var(--navy); }
  .brand__sub { display: block; font-size: 0.55em; letter-spacing: 6px; }

  .swoosh { position: absolute; inset: 0; }
  .contact {
    position: absolute;
    right: 36px;
    top: 220px;
    text-align: right;
    color: var(--white);
  }
  .contact__name { color: var(--amber); font-weight: 700; font-size: 22px; letter-spacing: 1px; }
  .contact__title { font-size: 15px; margin-bottom: 10px; }
  .contact__line {
    display: flex; justify-content: flex-end; align-items: center; gap: 8px;
    font-size: 15px; line-height: 22px;
  }
  .contact__line svg { width: 13px; height: 13px; fill: var(--amber); }
</style>
</head>
<body>
  <section class="card card--back" aria-label="Card back">
    <div class="back-texture" role="img" aria-label="Repeating brand pattern in tonal navy"></div>
    <div class="brand">
      <span class="brand__dot"></span>
      <span>SHIFTWELL<span class="brand__sub">CLINICS</span></span>
    </div>
  </section>

  <section class="card card--front" aria-label="Card front">
    <div class="brand">
      <span class="brand__dot"></span>
      <span>SHIFTWELL<span class="brand__sub">CLINICS</span></span>
    </div>
    <svg class="swoosh" viewBox="0 0 620 354" preserveAspectRatio="none" aria-hidden="true">
      <path d="M0 232 C160 228 300 170 430 158 C520 152 585 185 620 210 L620 354 L0 354 Z" fill="var(--navy)"/>
      <path d="M0 212 C120 240 280 185 420 150" fill="none" stroke="var(--amber)" stroke-width="6"/>
      <path d="M20 222 C190 220 320 152 450 146 C530 144 585 170 620 195" fill="none" stroke="var(--sky)" stroke-width="6"/>
      <path d="M220 205 C330 168 440 150 620 205" fill="none" stroke="var(--navy)" stroke-width="4"/>
    </svg>
    <div class="contact">
      <p class="contact__name">MARK ELLISON</p>
      <p class="contact__title">President</p>
      <p class="contact__line">555-010-4827
        <svg viewBox="0 0 24 24"><path d="M6.6 10.8a15 15 0 0 0 6.6 6.6l2.2-2.2c.3-.3.7-.4 1-.2 1.1.4 2.3.6 3.6.6.6 0 1 .4 1 1V20c0 .6-.4 1-1 1C10.6 21 3 13.4 3 4c0-.6.4-1 1-1h3.5c.6 0 1 .4 1 1 0 1.3.2 2.5.6 3.6.1.3 0 .7-.2 1z"/></svg>
      </p>
      <p class="contact__line">mark@shiftwell.com
        <svg viewBox="0 0 24 24"><path d="M2 5h20v14H2z M2 5l10 8 10-8" /></svg>
      </p>
      <p class="contact__line">www.shiftwell.com
        <svg viewBox="0 0 24 24"><circle cx="12" cy="12" r="10"/></svg>
      </p>
    </div>
  </section>
</body>
</html>
```